Lorvex Tilo medical cannibis cultivation company

tag - Tilo rise
Lorvex Tilo medical cannabis cultivation - logo is selected- can we please see bold examples with our selection. We are mainly dealing with medical companies and professionals. We would like to be stand out in the crowd with our designs. Welcome any and all attempts. Thanks

Target Market(s)

Medical and Professional

Industry/Entity Type

Medical And Science

Font styles to use
Sans Serif

Colors

Designer to choose colors to be used in the design.

Requirements
Must have
• Bright colour and be bold- Love the teal and magenta that is currently on the dark background design.
Nice to have
• shading and the 3D affect- The shadowed appearance.
Should not have
• Anything related to illegal activity or un professional manners

```html
<!DOCTYPE html>
<html lang="en">
<head>
<meta charset="utf-8">
<title>Lorvex Tilo — Business Card</title>
<link rel="stylesheet" href="https://fonts.googleapis.com/css2?family=Cinzel:wght@500;600&family=Cambo&display=swap">
<style>
  :root {
    --teal: #0aa9e1;
    --magenta: #9b4a98;
    --grey: #7d8287;
    --ink: #4a4d50;
    --card-light: #ffffff;
    --card-dark: #000000;
    --stage: #e9eaeb;
  }
  html, body {
    margin: 0;
    width: 1125px;
    height: 1200px;
    overflow: hidden;
    background: var(--stage);
  }
  .card {
    position: absolute;
    left: 150px;
    width: 826px;
    height: 471px;
    border-radius: 22px;
    overflow: hidden;
  }
  .card--front { top: 98px; background: var(--card-light); }
  .card--back { top: 631px; background: var(--card-dark); }

  .wordmark {
    position: absolute;
    margin: 0;
    font-family: "Cinzel", Georgia, serif;
    font-weight: 600;
    color: var(--teal);
    white-space: nowrap;
    line-height: 1;
  }
  .tagline {
    position: absolute;
    display: flex;
    align-items: center;
    gap: 10px;
    font-family: "Cinzel", Georgia, serif;
    font-weight: 500;
    color: var(--grey);
    letter-spacing: 3px;
    white-space: nowrap;
  }
  .tagline::before, .tagline::after {
    content: "";
    height: 2px;
    background: var(--grey);
    flex: 1;
  }

  .card--front .wordmark { left: 50px; top: 44px; font-size: 54px; }
  .card--front .tagline { left: 50px; top: 92px; width: 330px; font-size: 22px; }

  .person-name {
    position: absolute; left: 50px; top: 158px; margin: 0;
    font-family: "Cinzel", Georgia, serif; font-weight: 500;
    font-size: 34px; color: var(--teal); letter-spacing: 1px;
  }
  .person-role {
    position: absolute; left: 50px; top: 200px; margin: 0;
    font-family: "Cinzel", Georgia, serif; font-weight: 600;
    font-size: 22px; color: var(--magenta); letter-spacing: 1px;
  }
  .address {
    position: absolute; left: 50px; top: 236px; margin: 0;
    font-family: "Cambo", Georgia, serif; font-style: normal;
    font-size: 19px; line-height: 25px; color: var(--ink);
  }
  .contacts {
    position: absolute; left: 50px; top: 296px; margin: 0; padding: 0;
    list-style: none;
    font-family: "Cambo", Georgia, serif; font-size: 19px; color: var(--ink);
  }
  .contacts li { display: flex; align-items: center; height: 26.3px; }
  .contacts svg { width: 20px; height: 20px; margin-right: 12px; fill: var(--teal); }

  .emblem-area {
    position: absolute; left: 381px; top: 38px; width: 410px; height: 410px;
    border-radius: 50%;
    background: linear-gradient(135deg, rgba(155,74,152,0.18), rgba(10,169,225,0.18));
  }

  .ring {
    position: absolute; left: 310px; top: 92px; width: 206px; height: 206px;
  }
  .card--back .wordmark { left: 0; right: 0; top: 302px; text-align: center; font-size: 60px; }
  .card--back .tagline { left: 236px; top: 356px; width: 354px; font-size: 24px; }
</style>
</head>
<body>
  <section class="card card--front">
    <h1 class="wordmark">Lorvex Tilo</h1>
    <div class="tagline">Tilo rise</div>

    <p class="person-name">Maren Okafor</p>
    <p class="person-role">CEO/Founder</p>

    <address class="address">4210 Willowmere Road<br>Fairhaven, Oregon 58213</address>

    <ul class="contacts">
      <li><svg viewBox="0 0 24 24"><path d="M6.6 10.8a15 15 0 0 0 6.6 6.6l2.2-2.2a1 1 0 0 1 1-.25 11.4 11.4 0 0 0 3.6.57 1 1 0 0 1 1 1V20a1 1 0 0 1-1 1A17 17 0 0 1 3 4a1 1 0 0 1 1-1h3.5a1 1 0 0 1 1 1c0 1.25.2 2.45.57 3.57a1 1 0 0 1-.25 1z"/></svg>512 730 4186</li>
      <li><svg viewBox="0 0 24 24"><path d="M7 1h10a2 2 0 0 1 2 2v18a2 2 0 0 1-2 2H7a2 2 0 0 1-2-2V3a2 2 0 0 1 2-2zm0 3v14h10V4zm5 15.5a1.2 1.2 0 1 0 0 2.4 1.2 1.2 0 0 0 0-2.4z"/></svg>274 915 6032</li>
      <li><svg viewBox="0 0 24 24"><path d="M6 2h9l3 3v4H6zM3 10h18a1 1 0 0 1 1 1v8a1 1 0 0 1-1 1h-2v-3H5v3H3a1 1 0 0 1-1-1v-8a1 1 0 0 1 1-1zm4 8h10v4H7z"/></svg>390 261 8457</li>
      <li><svg viewBox="0 0 24 24"><path d="M2 5h20v14H2zm2 2v.4l8 5.2 8-5.2V7zm0 2.8V17h16V9.8l-8 5.2z"/></svg>maren@lorvextilo.com</li>
      <li><svg viewBox="0 0 24 24"><path d="M12 2a10 10 0 1 0 0 20 10 10 0 0 0 0-20zm-1 17.9A8 8 0 0 1 4.2 10.6L9 15.4v1a2 2 0 0 0 2 2zm6.9-2.5A2 2 0 0 0 16 16h-1v-3a1 1 0 0 0-1-1H8v-2h2a1 1 0 0 0 1-1V7h2a2 2 0 0 0 2-2v-.4a8 8 0 0 1 2.9 12.8z"/></svg>www.lorvextilo.com</li>
    </ul>

    <div class="emblem-area" role="img" aria-label="Large brand emblem area in magenta and teal"></div>
  </section>

  <section class="card card--back">
    <svg class="ring" viewBox="0 0 206 206" aria-hidden="true">
      <circle cx="103" cy="103" r="99" fill="none" stroke="var(--grey)" stroke-width="5"/>
    </svg>
    <h2 class="wordmark">Lorvex Tilo</h2>
    <div class="tagline">Tilo rise</div>
  </section>
</body>
</html>
```